Physiotherapy Referral Pad

-Need a referral pad for physiotherapy to be provided to doctors' offices. I would like it to be simple, not too cluttered and sharp looking so doctors can quickly complete it for clients.

-I have attached my logo which I would like to include. I have also included my business cards to keep the style, font, colors etc consistent.

-I would like to include my slogan
From Our Home To Yours

-I would like it to include services options with tick boxes for Mobile, Clinic, Telehealth, NRPDLA

-I would like for it to say Call to Book or Book Online

-I would like it to include my clinic address:
472 Marrow Crescent
Whitehorse, YT
Y2B3K9

-I would like it to include my contact info:
Glen Ostrow BSc(kin), MPT, CAFCI, IMS
(867)555-0142
physio@ostrowtherapy.ca

-I would like lines for the following:
Patient Name:
Diagnosis/Recommendations:
(extra lines to fill out patient info)

Physician Signature
Date

Target Market(s)

Physicians to refer clients to physiotherapy

Industry/Entity Type

Physical Therapy

Requirements
Must have
• Clean, concise, easy to look at and find pertinant categories for physicians
Nice to have
• Ostrow Therapy color scheme. Please see business cards and website as needed
Should not have
• Not too cluttered or wordy

```html
<!DOCTYPE html>
<html lang="en">
<head>
<meta charset="utf-8">
<title>Ostrow Therapy – Physiotherapy Referral Pad</title>
<link rel="stylesheet" href="https://fonts.googleapis.com/css2?family=Libre+Baskerville:wght@400;700&family=Montserrat:wght@500&display=swap">
<style>
  :root {
    --brand-blue: #243e8e;
    --brand-green: #145334;
    --rule: #555a66;
    --paper: #ffffff;
    --backdrop: #f1f2f4;
    --serif: "Libre Baskerville", Georgia, serif;
    --sans: "Montserrat", Arial, sans-serif;
  }
  * { box-sizing: border-box; margin: 0; padding: 0; }
  html, body { width: 1200px; height: 1200px; overflow: hidden; background: var(--backdrop); }
  .referral-pad {
    position: absolute; left: 243px; top: 95px;
    width: 714px; height: 1010px;
    background: var(--paper);
    overflow: hidden;
    font-family: var(--serif);
  }
  .pad-header { position: absolute; left: 0; top: 0; width: 714px; height: 174px; }
  .brand-name {
    position: absolute; left: 60px; top: 52px; width: 200px;
    text-align: center; color: var(--brand-green);
    font-family: var(--serif); font-weight: 700; font-size: 27px; line-height: 1.15;
    letter-spacing: 1px; text-transform: uppercase;
  }
  .clinic-contact {
    position: absolute; left: 465px; top: 40px;
    color: #fff; font-family: var(--sans); font-weight: 500; font-size: 13px; line-height: 16px;
    list-style: none;
  }
  .clinic-contact .address { margin-bottom: 6px; }
  .clinic-contact li { display: flex; align-items: center; gap: 4px; }
  .clinic-contact svg { width: 11px; height: 11px; flex: none; }
  .practitioner { position: absolute; top: 240px; left: 0; width: 714px; text-align: center; }
  .practitioner-name { color: var(--brand-green); font-weight: 700; font-size: 36px; letter-spacing: 0.5px; text-transform: uppercase; }
  .credentials { color: var(--brand-blue); font-weight: 700; font-size: 13px; margin-top: 4px; }
  .service-options {
    position: absolute; top: 326px; left: 0; width: 714px;
    display: flex; justify-content: center; gap: 10px; list-style: none;
    color: var(--brand-blue); font-weight: 700; font-size: 18px; letter-spacing: 0.5px;
  }
  .service-options li { display: flex; align-items: center; gap: 6px; }
  .tick-box { width: 16px; height: 16px; border: 2px solid var(--brand-green); }
  .field-label {
    position: absolute; color: var(--brand-blue); font-weight: 700; font-size: 16px;
    font-variant: small-caps; letter-spacing: 0.8px; white-space: nowrap;
  }
  .fill-line { position: absolute; height: 0; border-top: 1.4px solid var(--rule); }
  .booking-call {
    position: absolute; top: 924px; left: 0; width: 714px; text-align: center;
    color: var(--brand-green); font-weight: 700; font-size: 18px; font-variant: small-caps; letter-spacing: 2px;
  }
  .slogan-band {
    position: absolute; left: 0; top: 964px; width: 714px; height: 46px;
    background: var(--brand-blue); color: #fff;
    display: flex; align-items: center; justify-content: center;
    font-weight: 700; font-size: 18px; letter-spacing: 4px; text-transform: uppercase;
  }
</style>
</head>
<body>
<main class="referral-pad">
  <header>
    <svg class="pad-header" viewBox="0 0 714 174" aria-hidden="true">
      <polygon points="0,0 82,0 40,174 0,174" fill="var(--brand-green)"/>
      <polygon points="294,0 714,0 714,174 250,174" fill="var(--brand-blue)"/>
    </svg>
    <div class="brand-name">Ostrow<br>Therapy</div>
    <ul class="clinic-contact">
      <li class="address">472 Marrow Crescent<br>Whitehorse, YT Y2B3K9</li>
      <li><svg viewBox="0 0 12 12"><circle cx="6" cy="6" r="6" fill="#fff"/><path d="M3.8 3.2l1.2 1.1-.6.9c.4.9 1.1 1.6 2 2l.9-.6 1.1 1.2-.8.9C5.6 8.5 3.5 6.4 3.3 4z" fill="var(--brand-blue)"/></svg>(867)555-0142</li>
      <li><svg viewBox="0 0 12 12"><circle cx="6" cy="6" r="6" fill="#fff"/><rect x="3" y="4" width="6" height="4.2" fill="none" stroke="var(--brand-blue)" stroke-width="0.9"/><path d="M3 4l3 2.3L9 4" fill="none" stroke="var(--brand-blue)" stroke-width="0.9"/></svg>physio@ostrowtherapy.ca</li>
      <li><svg viewBox="0 0 12 12"><circle cx="6" cy="6" r="6" fill="#fff"/><circle cx="6" cy="6" r="3" fill="none" stroke="var(--brand-blue)" stroke-width="0.9"/><path d="M3 6h6M6 3v6" stroke="var(--brand-blue)" stroke-width="0.7"/></svg>www.ostrowtherapy.ca</li>
    </ul>
  </header>

  <section class="practitioner">
    <h1 class="practitioner-name">Glen Ostrow</h1>
    <p class="credentials">BSc(kin), MPT, CAFCI, IMS</p>
  </section>

  <ul class="service-options">
    <li><span class="tick-box"></span>MOBILE</li>
    <li><span class="tick-box"></span>CLINIC</li>
    <li><span class="tick-box"></span>TELEHEALTH</li>
    <li><span class="tick-box"></span>NRPDLA</li>
  </ul>

  <section class="referral-fields">
    <span class="field-label" style="left:73px; top:412px; font-variant:normal;">PATIENT NAME:</span>
    <span class="fill-line" style="left:254px; width:383px; top:438px;"></span>
    <span class="fill-line" style="left:73px; width:564px; top:497px;"></span>

    <span class="field-label" style="left:73px; top:532px;">Diagnosis/Recommendations:</span>
    <span class="fill-line" style="left:406px; width:231px; top:558px;"></span>
    <span class="fill-line" style="left:73px; width:564px; top:616px;"></span>
    <span class="fill-line" style="left:77px; width:564px; top:674px;"></span>

    <span class="field-label" style="left:76px; top:718px;">Physician Signature</span>
    <span class="fill-line" style="left:316px; width:323px; top:744px;"></span>

    <span class="field-label" style="left:76px; top:778px;">Date</span>
    <span class="fill-line" style="left:137px; width:502px; top:804px;"></span>
  </section>

  <p class="booking-call">Call to Book or Book Online</p>
  <footer class="slogan-band">From Our Home to Yours</footer>
</main>
</body>
</html>
```